Indy Film Production Company/Studio

We need a business card designed from an existing logo. We are a digital studio/production company that caters to creating genre entertainment, like Action, Horror, and martial arts. The card along with the logo will be used to Brand the company from letter heads to banners. The design will also be used for postcards and Brochures. It should be professional and masculine.
Updates

Thank you to all the designers who have participated. I'm narrowing down who it will be. Thank you again.

Target Market(s)

Investors, Networks, Producers, and actors

Industry/Entity Type

Film Production

Contact Information for Business Card

Teodoro Valbuena
Producer/Writer/Director
www.kestrelpicturehouse.example

Requirements
Must have
• Website address, plain circle with /kestrelpictures icon and plain circle with @kestrelpictures icon possibly in the back of the card.
Nice to have
• Logline of Company: Follow The Action.

```html
<!DOCTYPE html>
<html lang="en">
<head>
<meta charset="utf-8">
<title>Kestrel Picture House – Business Card</title>
<link rel="stylesheet" href="https://fonts.googleapis.com/css2?family=Open+Sans:wght@400;600;800&display=swap">
<style>
  :root {
    --backdrop: #ece8e3;
    --kraft-light: #c9a87a;
    --kraft: #bf9d6d;
    --kraft-dark: #b08d5e;
    --ink: #141210;
  }
  * { box-sizing: border-box; margin: 0; padding: 0; }
  html, body {
    width: 1200px; height: 900px; overflow: hidden;
    background: var(--backdrop);
    font-family: "Open Sans", Arial, sans-serif;
    color: var(--ink);
  }
  .canvas { position: relative; width: 1200px; height: 900px; }
  .card {
    position: absolute;
    width: 556px; height: 342px;
    background: radial-gradient(ellipse at 40% 35%, var(--kraft-light), var(--kraft) 60%, var(--kraft-dark));
    box-shadow: 0 6px 18px rgba(0,0,0,.18);
  }
  .card--front { left: 238px; top: 62px; }
  .card--back { left: 458px; top: 518px; width: 560px; }

  .wordmark {
    position: absolute;
    font-weight: 800;
    text-transform: uppercase;
    text-align: center;
    line-height: 1.05;
    letter-spacing: .02em;
    color: var(--ink);
  }
  .card--front .wordmark { left: 150px; top: 44px; width: 270px; font-size: 36px; }
  .card--back .wordmark { left: 140px; top: 102px; width: 300px; font-size: 38px; }

  .identity { position: absolute; left: 0; width: 556px; top: 178px; text-align: center; padding-left: 20px; }
  .identity__name { font-size: 18px; font-weight: 600; line-height: 24px; }
  .identity__title { font-size: 14px; font-weight: 400; line-height: 18px; }

  .contacts { position: absolute; left: 175px; top: 239px; list-style: none; font-size: 14px; }
  .contacts li { display: flex; align-items: center; height: 20px; gap: 7px; }
  .contacts svg { width: 11px; height: 11px; fill: var(--ink); flex: none; }

  .social {
    position: absolute; left: 0; width: 560px; top: 262px;
    display: flex; justify-content: center; gap: 22px;
    list-style: none; font-size: 12px; line-height: 16px;
  }
  .social li { display: flex; align-items: center; gap: 6px; }
  .social__dot { width: 12px; height: 12px; border-radius: 50%; background: var(--ink); flex: none; }
</style>
</head>
<body>
<main class="canvas">
  <section class="card card--front" aria-label="Business card front">
    <div class="wordmark">Kestrel<br>Picture House</div>
    <div class="identity">
      <p class="identity__name">Teodoro Valbuena</p>
      <p class="identity__title">Producer/Writer/Director</p>
    </div>
    <ul class="contacts">
      <li>
        <svg viewBox="0 0 24 24" aria-hidden="true"><path d="M6.6 10.8a15.1 15.1 0 0 0 6.6 6.6l2.2-2.2c.3-.3.7-.4 1-.2 1.1.4 2.3.6 3.6.6.6 0 1 .4 1 1V20c0 .6-.4 1-1 1A17 17 0 0 1 3 4c0-.6.4-1 1-1h3.5c.6 0 1 .4 1 1 0 1.3.2 2.5.6 3.6.1.3 0 .7-.2 1z"/></svg>
        <span>044-555 010 274</span>
      </li>
      <li>
        <svg viewBox="0 0 24 24" aria-hidden="true"><path d="M2 5h20v14H2z"/><path d="M3.5 6.5l8.5 6.5 8.5-6.5" fill="none" stroke="#bf9d6d" stroke-width="2"/></svg>
        <span>info@kestrelpicturehouse.example</span>
      </li>
      <li>
        <svg viewBox="0 0 24 24" aria-hidden="true"><circle cx="12" cy="12" r="10"/><path d="M2 12h20M12 2c-3 3-3 17 0 20M12 2c3 3 3 17 0 20" fill="none" stroke="#bf9d6d" stroke-width="1.6"/></svg>
        <span>www.kestrelpicturehouse.example</span>
      </li>
    </ul>
  </section>

  <section class="card card--back" aria-label="Business card back">
    <div class="wordmark">Kestrel<br>Picture House</div>
    <ul class="social">
      <li><span>www.kestrelpicturehouse.example</span></li>
      <li><span class="social__dot" aria-hidden="true"></span><span>/kestrelpictures</span></li>
      <li><span class="social__dot" aria-hidden="true"></span><span>@kestrelpictures</span></li>
    </ul>
  </section>
</main>
</body>
</html>
```